Business Card Design

We need a business card designed for our new company. Prefer a black card with white logo & writing.

Contact Information for Business Card

Ted Galloway, address: 7-4812 Fernhollow Road, Abbotsford, BC, V3K 8R2, Office Phone: 604-712-3390, Cell: 604-947-2164, Email: ted@resinworkshub.ca

Colors

Designer to choose only greyscale colors for use in the design.

```html
<!DOCTYPE html>
<html lang="en">
<head>
<meta charset="utf-8">
<title>Resin Works Hub – Business Card</title>
<link href="https://fonts.googleapis.com/css2?family=Montserrat:wght@400;800&display=swap" rel="stylesheet">
<style>
  :root {
    --backdrop: #2b2b2b;
    --card: #141414;
    --ink: #ffffff;
    --ink-soft: #e6e6e6;
    --rule: #9a9a9a;
  }
  * { margin: 0; padding: 0; box-sizing: border-box; }
  html, body {
    width: 1200px;
    height: 900px;
    overflow: hidden;
    background: var(--backdrop);
    font-family: "Montserrat", sans-serif;
  }
  .canvas {
    position: relative;
    width: 1200px;
    height: 900px;
    display: flex;
    align-items: center;
    justify-content: center;
  }
  .business-card {
    position: relative;
    width: 940px;
    height: 537px;
    background: var(--card);
    color: var(--ink);
    box-shadow: 0 18px 40px rgba(0,0,0,0.45);
  }
  .accent-bar {
    position: absolute;
    width: 24px;
    background: var(--ink);
  }
  .accent-bar--left { left: 40px; top: 70px; height: 250px; }
  .accent-bar--right { right: 40px; top: 250px; height: 230px; }

  .brand {
    position: absolute;
    left: 110px;
    top: 0;
    width: 390px;
    height: 100%;
    display: flex;
    align-items: center;
    justify-content: center;
    gap: 16px;
  }
  .brand-mark {
    width: 30px;
    height: 30px;
    background: var(--ink);
    flex: none;
  }
  .brand-name {
    font-weight: 800;
    font-size: 40px;
    line-height: 1.05;
    letter-spacing: 0.5px;
    text-transform: uppercase;
    color: var(--ink);
  }

  .divider {
    position: absolute;
    left: 520px;
    top: 110px;
    width: 1px;
    height: 300px;
    background: var(--rule);
  }

  .contact {
    position: absolute;
    left: 570px;
    top: 120px;
    width: 320px;
  }
  .contact-name {
    font-weight: 800;
    font-size: 34px;
    letter-spacing: 0.5px;
    margin-bottom: 28px;
  }
  .contact-list { list-style: none; }
  .contact-item {
    display: flex;
    align-items: center;
    gap: 10px;
    font-size: 21px;
    line-height: 1.45;
    color: var(--ink-soft);
  }
  .contact-icon { width: 17px; height: 17px; flex: none; fill: var(--ink); }
  .contact-address {
    margin-top: 22px;
    font-style: normal;
    font-size: 21px;
    line-height: 1.45;
    color: var(--ink-soft);
  }
</style>
</head>
<body>
<main class="canvas">
  <section class="business-card">
    <div class="accent-bar accent-bar--left"></div>
    <div class="accent-bar accent-bar--right"></div>

    <div class="brand">
      <span class="brand-mark"></span>
      <span class="brand-name">Resin Works<br>Hub</span>
    </div>

    <div class="divider"></div>

    <div class="contact">
      <h1 class="contact-name">Ted Galloway</h1>
      <ul class="contact-list">
        <li class="contact-item">
          <svg class="contact-icon" viewBox="0 0 24 24" aria-hidden="true"><path d="M6.6 10.8a15.1 15.1 0 0 0 6.6 6.6l2.2-2.2a1 1 0 0 1 1-.25 11.4 11.4 0 0 0 3.6.57 1 1 0 0 1 1 1V20a1 1 0 0 1-1 1A17 17 0 0 1 3 4a1 1 0 0 1 1-1h3.5a1 1 0 0 1 1 1c0 1.25.2 2.46.57 3.6a1 1 0 0 1-.25 1z"/></svg>
          604-712-3390
        </li>
        <li class="contact-item">
          <svg class="contact-icon" viewBox="0 0 24 24" aria-hidden="true"><path d="M7 1h10a2 2 0 0 1 2 2v18a2 2 0 0 1-2 2H7a2 2 0 0 1-2-2V3a2 2 0 0 1 2-2zm0 3v14h10V4zm5 15.5a1.2 1.2 0 1 0 0 2.4 1.2 1.2 0 0 0 0-2.4z"/></svg>
          604-947-2164
        </li>
        <li class="contact-item">
          <svg class="contact-icon" viewBox="0 0 24 24" aria-hidden="true"><path d="M2 5h20v14H2zm2 2v.4l8 5.2 8-5.2V7zm0 2.8V17h16V9.8l-8 5.2z"/></svg>
          ted@resinworkshub.ca
        </li>
      </ul>
      <address class="contact-address">
        7-4812 Fernhollow Road,<br>
        Abbotsford, BC, V3K 8R2
      </address>
    </div>
  </section>
</main>
</body>
</html>
```